Cover for Lanterns Along the Quiet Shore of Being

Cover for a book that describes everything that happens to a person, from pre-birth life plans through growing in compassion and wisdom to death and living in the afterlife. The information is revealed in messages from people living in the life after this life. The title is Lessons Gathered From Every Season of Your Existence: Shared by Voices Dwelling Beyond the Veil. Author is T. Wesley Prandt. Book size is 6 by 9.

Target Market(s)

General

Font styles to use
Serif

```html
<!DOCTYPE html>
<html lang="en">
<head>
<meta charset="utf-8">
<title>Lanterns Along the Quiet Shore of Being — Book Cover</title>
<link href="https://fonts.googleapis.com/css2?family=Oswald:wght@400;600&family=Josefin+Sans:wght@300&display=swap" rel="stylesheet">
<style>
  :root {
    --sky-top: #2a2a55;
    --sky-mid: #3b3a70;
    --sky-low: #4a4a80;
    --tree-dark: #141318;
    --text-white: #ffffff;
    --veil-light: rgba(255, 255, 255, 0.10);
    --veil-dark: rgba(10, 10, 14, 0.35);
  }
  html, body {
    margin: 0;
    padding: 0;
    width: 800px;
    height: 1200px;
    overflow: hidden;
    background: #1e1d3a;
  }
  .cover {
    position: relative;
    width: 800px;
    height: 1200px;
    overflow: hidden;
  }
  .night-sky {
    position: absolute;
    inset: 0;
    background:
      radial-gradient(ellipse 420px 300px at 440px 920px, var(--tree-dark) 0%, rgba(20,19,24,0.92) 55%, rgba(20,19,24,0) 100%),
      radial-gradient(ellipse 520px 160px at 400px 1160px, var(--tree-dark) 0%, rgba(20,19,24,0.8) 60%, rgba(20,19,24,0) 100%),
      linear-gradient(180deg, var(--sky-top) 0%, var(--sky-mid) 55%, var(--sky-low) 100%);
  }
  .facets {
    position: absolute;
    inset: 0;
  }
  .cover-text {
    position: absolute;
    left: 81px;
    top: 108px;
    width: 640px;
    color: var(--text-white);
  }
  .title {
    margin: 0;
    font-family: 'Oswald', 'Arial Narrow', sans-serif;
    font-weight: 600;
    font-size: 58px;
    line-height: 71px;
    letter-spacing: 2px;
    text-transform: uppercase;
  }
  .subtitle {
    margin: 10px 0 0;
    font-family: 'Josefin Sans', 'Helvetica', sans-serif;
    font-weight: 300;
    font-size: 25px;
    line-height: 34px;
    letter-spacing: 5px;
    text-transform: uppercase;
  }
  .rule {
    width: 383px;
    height: 5px;
    margin: 36px 0 0;
    background: var(--text-white);
  }
  .author {
    margin: 24px 0 0;
    font-family: 'Oswald', 'Arial Narrow', sans-serif;
    font-weight: 400;
    font-size: 24px;
    letter-spacing: 5px;
    text-transform: uppercase;
  }
</style>
</head>
<body>
  <main class="cover">
    <div class="night-sky" role="img" aria-label="Starry night sky over the dark silhouette of a tree"></div>
    <svg class="facets" width="800" height="1200" viewBox="0 0 800 1200" aria-hidden="true">
      <polygon points="800,385 800,1200 0,1200 0,860 190,1090" fill="var(--veil-light)"/>
      <polygon points="510,732 800,1200 0,1200 0,1200 190,1090" fill="var(--veil-dark)"/>
      <polygon points="0,860 235,1090 0,1200" fill="var(--veil-light)"/>
    </svg>
    <header class="cover-text">
      <h1 class="title">Lessons Gathered From Every Season of Your Existence:</h1>
      <p class="subtitle">Shared by Voices Dwelling Beyond the Veil</p>
      <div class="rule"></div>
      <p class="author">By T. Wesley Prandt</p>
    </header>
  </main>
</body>
</html>
```